Local Flower Farm Needs Business Card Design

I need business cards designed for a flower farm based in Eudora, Kansas.
Business Info:
We are a local cut flower farm located in Eudora, Kansas, founded by Corinne Haldwick. What started as a passion for agriculture and search for more joy in daily life has blossomed into a small business dedicated to providing the community with beautiful, fresh, and sustainable flowers. We specialize in local, seasonal blooms, ensuring that every petal reflects the care and dedication we pour into our craft. Our mission is to deliver the highest quality flowers directly to our customers through local farmers markets and to florists who share our commitment to sustainability. Join us in celebrating the beauty of nature, one bloom at a time!
Contact Details:
Corinne Haldwick
Owner
Phone 913-555-0147
Facebook: Rosalind Thorpe Gardens
Instagram: @RosalindThorpeGardens
Website: RosalindThorpeGardens.example
Target Market(s)
Wholesale to Florists and Direct to Consumer via Farmers Market
Industry/Entity Type
Florist, Farm
Contact Information for Business Card
Name, Contact Info, Logo
Look and feel
Each slider illustrates characteristics of the customer's brand and the style your logo design should communicate.

```html
<!DOCTYPE html>
<html lang="en">
<head>
<meta charset="utf-8">
<title>Rosalind Thorpe Gardens – Business Card</title>
<link href="https://fonts.googleapis.com/css2?family=Playfair+Display:wght@400;700&family=Libre+Caslon+Text:wght@400&display=swap" rel="stylesheet">
<style>
  :root {
    --bg: #3a3a3c;
    --teal-deep: #0c262b;
    --teal-ink: #0f2e33;
    --teal-emboss: #17434a;
    --paper: #ffffff;
    --rule: #5d7479;
  }
  * { box-sizing: border-box; margin: 0; padding: 0; }
  html, body { width: 1200px; height: 689px; overflow: hidden; }
  body {
    background: var(--bg);
    display: flex;
    align-items: center;
    justify-content: center;
    gap: 40px;
    font-family: "Libre Caslon Text", Georgia, serif;
  }
  .card {
    width: 540px;
    height: 310px;
    border-radius: 22px;
    position: relative;
    overflow: hidden;
  }
  /* Back side */
  .card-back {
    background: var(--teal-deep);
    display: flex;
    align-items: center;
    justify-content: center;
  }
  .emboss-seal {
    width: 200px;
    height: 200px;
    border-radius: 50%;
    border: 1.5px solid var(--teal-emboss);
    display: flex;
    align-items: center;
    justify-content: center;
    text-align: center;
    color: var(--teal-emboss);
    font-family: "Playfair Display", Georgia, serif;
    font-weight: 400;
    font-size: 19px;
    line-height: 1.3;
    letter-spacing: 0.12em;
    text-transform: uppercase;
  }
  /* Front side */
  .card-front { background: var(--paper); color: var(--teal-ink); }
  .front-seal {
    position: absolute;
    left: 28px;
    top: 26px;
    width: 128px;
    height: 128px;
    border-radius: 50%;
    border: 1px solid var(--rule);
    display: flex;
    align-items: center;
    justify-content: center;
    text-align: center;
    font-family: "Playfair Display", Georgia, serif;
    font-size: 12px;
    line-height: 1.35;
    letter-spacing: 0.12em;
    text-transform: uppercase;
  }
  .feature-name {
    position: absolute;
    right: 26px;
    top: 20px;
    text-align: right;
    font-family: "Playfair Display", Georgia, serif;
    font-weight: 700;
    font-size: 58px;
    line-height: 0.98;
    color: var(--teal-ink);
  }
  .contact {
    position: absolute;
    left: 30px;
    bottom: 22px;
  }
  .contact-name {
    font-family: "Playfair Display", Georgia, serif;
    font-weight: 700;
    font-size: 21px;
  }
  .contact-role { font-size: 12px; margin: 2px 0 8px; }
  .contact-list { list-style: none; font-size: 12.5px; line-height: 1.6; }
  .contact-list li { display: flex; align-items: center; gap: 7px; }
  .contact-list svg { width: 12px; height: 12px; flex: none; }
  .social-mark {
    width: 11px; height: 11px; flex: none;
    background: var(--teal-ink);
  }
  .social-mark.round { border-radius: 50%; }
</style>
</head>
<body>
  <section class="card card-back" aria-label="Card back">
    <div class="emboss-seal">Rosalind<br>Thorpe<br>Gardens</div>
  </section>

  <section class="card card-front" aria-label="Card front">
    <div class="front-seal">Rosalind<br>Thorpe<br>Gardens</div>
    <div class="feature-name">Rosalind<br>Thorpe<br>Gardens</div>
    <div class="contact">
      <p class="contact-name">Corinne Haldwick</p>
      <p class="contact-role">Owner</p>
      <ul class="contact-list">
        <li>
          <svg viewBox="0 0 24 24" aria-hidden="true"><path fill="#0f2e33" d="M6.6 10.8a15 15 0 0 0 6.6 6.6l2.2-2.2a1 1 0 0 1 1-.25 11.4 11.4 0 0 0 3.6.57 1 1 0 0 1 1 1V20a1 1 0 0 1-1 1A17 17 0 0 1 3 4a1 1 0 0 1 1-1h3.5a1 1 0 0 1 1 1c0 1.25.2 2.45.57 3.57a1 1 0 0 1-.25 1z"/></svg>
          913-555-0147
        </li>
        <li>
          <svg viewBox="0 0 24 24" aria-hidden="true"><circle cx="12" cy="12" r="10" fill="none" stroke="#0f2e33" stroke-width="2.2"/><path d="M2 12h20M12 2c3 3 3 17 0 20M12 2c-3 3-3 17 0 20" fill="none" stroke="#0f2e33" stroke-width="1.8"/></svg>
          RosalindThorpeGardens.example
        </li>
        <li><span class="social-mark"></span>Rosalind Thorpe Gardens</li>
        <li><span class="social-mark round"></span>@RosalindThorpeGardens</li>
      </ul>
    </div>
  </section>
</body>
</html>
```